Business Card & Letterhead Design

We a financial advice company based in Australia. We provide advice to wealthy farmers.

We are changing our business name FROM Brightvale Financial TO Tallowmere Wealth and we need a new letterhead and double sided business card design

Attached is designs from our previous branding (Brightvale Financial) as it includes all the details we require on the new Tallowmere Wealth business cards and letterhead.

Need extra days to review

```html
<!DOCTYPE html>
<html lang="en">
<head>
<meta charset="utf-8">
<title>Tallowmere Wealth – Stationery</title>
<link href="https://fonts.googleapis.com/css2?family=Lato:wght@400&family=Tinos:wght@400;700&display=swap" rel="stylesheet">
<style>
  :root{
    --bg:#efefef;
    --paper:#ffffff;
    --charcoal:#464646;
    --stripe:#6f6f6f;
    --ink:#555555;
    --ink-dark:#333333;
    --rule:#bdbdbd;
    --on-dark:#ffffff;
  }
  html,body{margin:0;padding:0;overflow:hidden}
  body{width:1200px;height:1200px;background:var(--bg);position:relative;font-family:"Tinos",serif;color:var(--ink)}
  .sheet{position:absolute;background:var(--paper);overflow:hidden}
  .swoop{position:absolute;left:0;top:0;display:block}
  .abs{position:absolute;margin:0;white-space:nowrap}

  /* brand name lockup: square beside name, plain descriptor below */
  .brand{color:var(--ink)}
  .brand .row{display:flex;align-items:center;gap:8px}
  .brand .square{display:block;background:currentColor;flex:none}
  .brand .name{font-family:"Tinos",serif;font-weight:400;line-height:1}
  .brand .tag{display:block;font-family:"Tinos",serif;line-height:1;margin-top:5px}

  /* letterhead */
  .letterhead{left:43px;top:175px;width:600px;height:850px}
  .entity{left:24px;top:22px;font-family:"Lato",sans-serif;font-size:9.6px;line-height:12.6px;color:var(--on-dark)}
  .abn{left:24px;top:56px;font-family:"Lato",sans-serif;font-size:9.6px;color:var(--on-dark)}
  .lh-brand{right:24px;top:112px;text-align:right}
  .lh-brand .row{justify-content:flex-end}
  .lh-brand .square{width:14px;height:14px}
  .lh-brand .name{font-size:20px}
  .lh-brand .tag{font-size:9px}

  .lh-address{left:24px;top:739px;font-size:9.7px;line-height:12.4px;color:#666}
  .lh-licence{right:24px;top:752px;font-size:9.7px;line-height:12.4px;color:#666;text-align:right}
  .lh-rule{left:24px;width:552px;top:798px;height:2px;background:var(--stripe)}
  .lh-contacts{left:36px;top:810px;display:flex;gap:26px;font-size:9.7px;color:#666}
  .lh-contacts span{display:flex;align-items:center;gap:6px}
  .ico{width:7px;height:7px;display:inline-block}

  /* business card front */
  .card{width:463px;height:264px}
  .card-front{left:691px;top:374px}
  .cf-brand{right:17px;top:74px;text-align:right}
  .cf-brand .row{justify-content:flex-end;gap:6px}
  .cf-brand .square{width:10px;height:10px}
  .cf-brand .name{font-size:14.5px}
  .cf-brand .tag{font-size:7px;margin-top:4px}
  .person{left:17px;top:118px;font-size:17.5px;font-weight:700;color:var(--ink-dark)}
  .person small{font-size:6px;font-weight:400;margin-left:4px;vertical-align:3px}
  .role{left:17px;top:141px;font-size:10.5px;color:#666}
  .status{right:17px;top:141px;font-size:10.5px;color:#666}
  .cf-rule{left:17px;top:164px;width:429px;height:1px;background:var(--rule)}
  .cf-rule-accent{left:17px;top:163.5px;width:149px;height:2px;background:var(--ink-dark)}
  .cf-contacts{left:17px;top:175px;font-size:10px;line-height:15px;color:#666}
  .cf-contacts span{display:flex;align-items:center;gap:6px}
  .cf-address{right:17px;top:195px;font-size:10.3px;line-height:13.2px;color:#666;text-align:right}

  /* business card back */
  .card-back{left:691px;top:679px;background:var(--charcoal);color:var(--on-dark)}
  .cb-brand{left:0;width:463px;top:100px;text-align:center;color:var(--on-dark)}
  .cb-brand .row{justify-content:center;gap:9px}
  .cb-brand .square{width:15px;height:15px}
  .cb-brand .name{font-size:21px}
  .cb-brand .tag{font-size:9px;margin-top:6px}
  .services{left:0;width:463px;top:170px;text-align:center;font-size:10.6px;line-height:13px}
  .cb-rule{left:211px;top:207px;width:41px;height:1px;background:var(--on-dark)}
  .licensee{left:0;width:463px;top:217px;text-align:center;font-size:10.6px;line-height:17px}
</style>
</head>
<body>

<!-- Letterhead -->
<section class="sheet letterhead">
  <svg class="swoop" width="600" height="150" viewBox="0 0 967 240" aria-hidden="true">
    <path d="M0 0 H967 V86 Q 560 40 0 236 Z" fill="#464646"/>
    <path d="M80 210 Q 470 62 967 94 V122 Q 540 66 80 210 Z" fill="#6f6f6f"/>
  </svg>
  <p class="abs entity">Marrowby Holdings Pty Ltd ATF The<br>Westerly Investment Trust T/AS Brightvale Financial</p>
  <p class="abs abn">ABN: 12 345 678 901</p>
  <div class="abs brand lh-brand">
    <div class="row"><span class="square"></span><span class="name">Tallowmere Wealth</span></div>
    <span class="tag">Strategic financial advice</span>
  </div>

  <p class="abs lh-address">Suite 4A, 18 Ferncliff St<br>Riverbend QLD 4101<br>PO Box 2150<br>Eastvale QLD 4102</p>
  <p class="abs lh-licence">Corporate Authorised<br>Representative of Keystone<br>Advice Partners Limited</p>
  <div class="abs lh-rule"></div>
  <div class="abs lh-contacts">
    <span><svg class="ico" viewBox="0 0 10 10"><path d="M2 1 L4 3 L3 4.5 Q4.5 6.5 5.5 7 L7 6 L9 8 L7.5 9.5 Q3 8.5 0.5 2.5 Z" fill="#444"/></svg>(07) 3000 1234</span>
    <span><svg class="ico" viewBox="0 0 10 10"><rect x="2" y="0.5" width="6" height="3" fill="#444"/><rect x="0.5" y="3.5" width="9" height="4" fill="#444"/><rect x="2" y="7" width="6" height="2.5" fill="#444"/></svg>(07) 3000 5678</span>
    <span><svg class="ico" viewBox="0 0 10 10"><rect x="0.5" y="2" width="9" height="6.5" fill="#444"/><path d="M1 2.5 L5 5.5 L9 2.5" stroke="#fff" fill="none"/></svg>admin@brightvalefinancial.com.au</span>
    <span><svg class="ico" viewBox="0 0 10 10"><circle cx="5" cy="5" r="4.5" fill="#444"/></svg>www.brightvalefinancial.com.au</span>
  </div>
</section>

<!-- Business card front -->
<section class="sheet card card-front">
  <svg class="swoop" width="463" height="110" viewBox="0 0 745 177" aria-hidden="true">
    <path d="M0 0 H745 V52 Q 420 20 0 165 Z" fill="#464646"/>
    <path d="M90 125 Q 380 36 745 60 V82 Q 400 40 90 125 Z" fill="#6f6f6f"/>
  </svg>
  <div class="abs brand cf-brand">
    <div class="row"><span class="square"></span><span class="name">Tallowmere Wealth</span></div>
    <span class="tag">Strategic financial advice</span>
  </div>
  <p class="abs person">Sam Harlow<small>B.Ag.Ec. Dip F.P. CFP®</small></p>
  <p class="abs role">Managing Director</p>
  <p class="abs status">Authorised Representative</p>
  <div class="abs cf-rule"></div>
  <div class="abs cf-rule-accent"></div>
  <div class="abs cf-contacts">
    <span><svg class="ico" viewBox="0 0 10 10"><path d="M2 1 L4 3 L3 4.5 Q4.5 6.5 5.5 7 L7 6 L9 8 L7.5 9.5 Q3 8.5 0.5 2.5 Z" fill="#444"/></svg>(07) 3000 1234</span>
    <span><svg class="ico" viewBox="0 0 10 10"><rect x="2" y="0.5" width="6" height="9" rx="1" fill="none" stroke="#444" stroke-width="1.4"/></svg>0400 555 012</span>
    <span><svg class="ico" viewBox="0 0 10 10"><rect x="2" y="0.5" width="6" height="3" fill="#444"/><rect x="0.5" y="3.5" width="9" height="4" fill="#444"/><rect x="2" y="7" width="6" height="2.5" fill="#444"/></svg>(07) 3000 5678</span>
    <span><svg class="ico" viewBox="0 0 10 10"><rect x="0.5" y="2" width="9" height="6.5" fill="#444"/><path d="M1 2.5 L5 5.5 L9 2.5" stroke="#fff" fill="none"/></svg>admin@brightvalefinancial.com.au</span>
    <span><svg class="ico" viewBox="0 0 10 10"><circle cx="5" cy="5" r="4.5" fill="#444"/></svg>www.brightvalefinancial.com.au</span>
  </div>
  <p class="abs cf-address">Suite 4A, 18 Ferncliff St<br>Riverbend QLD 4101<br>PO Box 2150<br>Eastvale QLD 4102</p>
</section>

<!-- Business card back -->
<section class="sheet card card-back">
  <div class="abs brand cb-brand">
    <div class="row"><span class="square"></span><span class="name">Tallowmere Wealth</span></div>
    <span class="tag">Strategic financial advice</span>
  </div>
  <p class="abs services">Life &amp; TPD Insurance Income Protection<br>Financial Planning Retirement Planning</p>
  <div class="abs cb-rule"></div>
  <p class="abs licensee">Keystone Advice Partners Limited<br>Australian Financial Services Licensee License Number 100001</p>
</section>

</body>
</html>
```